Website for Torvel Capital - investment banking firm

We have a corporate identity (thanks to Ravinka/31842) and want to extend that into a website design.  See the attached zipped files.
We have software folks in-house to do the coding.
See the attached Project Brief & Notes for more details.  Don't worry about the actual text - lorem ipsum will be fine.
The server will be Apache.
Thank you!
Desmond

Industry/Entity Type
Investment

```html
<!DOCTYPE html>
<html lang="en">
<head>
<meta charset="utf-8">
<title>Torvel Capital</title>
<link href="https://fonts.googleapis.com/css2?family=Ubuntu:wght@300;400&display=swap" rel="stylesheet">
<style>
:root{
  --brand-blue:#1f4e8f;
  --button-blue:#234b8d;
  --ink:#2d2d2d;
  --body-ink:#4a4a4a;
  --nav-ink:#333;
  --panel:#ffffff;
  --band:#f2f2f2;
  --rule:#dcdcdc;
  --logo-grey:#8a8a8a;
  --sky-top:#c9c6d6;
  --sky-mid:#dcd9e6;
}
*{margin:0;padding:0;box-sizing:border-box}
html,body{width:1034px;height:1200px;overflow:hidden;background:#fff}
body{font-family:'Ubuntu',sans-serif;color:var(--ink);font-weight:300}
.page{position:relative;width:1034px;height:1200px;overflow:hidden;background:#fff}
.site-header{position:absolute;left:0;top:0;width:1034px;height:93px;background:var(--brand-blue)}
.brand{position:absolute;left:107px;top:27px;display:flex;align-items:center;gap:12px;color:#fff;font-family:'Ubuntu',sans-serif;font-weight:400;font-size:26px}
.brand-square{width:36px;height:36px;background:#fff}
.contact{position:absolute;right:90px;top:25px;text-align:right;color:#fff;font-size:12px;line-height:16px;font-weight:300}
.hero{position:absolute;left:0;top:93px;width:1034px;height:520px;
  background:linear-gradient(180deg,var(--sky-top) 0%,var(--sky-mid) 35%,#d6d3df 55%,#e7e5ec 80%,#fff 100%)}
.main-nav{position:absolute;left:75px;top:93px;width:883px;height:39px;background:linear-gradient(#fff,#ececec);border-radius:0 0 6px 6px;display:flex;align-items:center;padding-left:21px}
.main-nav a{color:var(--nav-ink);text-decoration:none;font-size:14px;font-weight:300;margin-right:35px}
.hero-caption{position:absolute;left:234px;top:349px;width:583px;height:75px;background:rgba(255,255,255,.35);text-align:center;font-size:18.5px;line-height:26px;padding-top:13px;color:#3a3a3a}
.hero-dots{position:absolute;left:496px;top:546px;display:flex;gap:10px}
.hero-dots span{width:8px;height:8px;border-radius:50%;background:var(--brand-blue)}
.hero-dots span.off{background:#a9a9b0}
.content{position:absolute;left:76px;top:590px;width:882px;height:560px;background:linear-gradient(rgba(255,255,255,0),var(--panel) 20px)}
h2{font-weight:300;font-size:19px;color:var(--ink);position:absolute}
p.copy{position:absolute;font-size:11.6px;line-height:16.5px;color:var(--body-ink)}
.btn{position:absolute;height:26px;padding:0 8px;background:var(--button-blue);color:#fff;font-size:11.5px;line-height:26px;border-radius:3px;text-decoration:none}
.world-map{position:absolute;left:166px;top:711px;width:317px;height:177px;background:radial-gradient(ellipse at 50% 45%,#bdbdbd,#dedede 60%,#fff 80%)}
.divider{position:absolute;left:598px;top:603px;width:1px;height:315px;background:var(--rule)}
.service h3{position:absolute;font-weight:300;font-size:19px;color:var(--ink)}
.service svg{position:absolute}
.clients{position:absolute;left:76px;top:1095px;width:882px;height:54px;background:var(--band)}
.clients h2{left:37px;top:16px}
.client-list{position:absolute;left:161px;top:18px;display:flex;gap:22px;align-items:center}
.client-list span{font-size:14.5px;font-weight:400;color:var(--logo-grey);display:flex;align-items:center;gap:5px}
.client-list i{display:inline-block;width:10px;height:10px;border-radius:50%;background:var(--logo-grey)}
.site-footer{position:absolute;left:0;top:1149px;width:1034px;height:51px;background:var(--brand-blue);color:#fff;font-size:11px}
.footer-nav{position:absolute;left:112px;top:18px;display:flex}
.footer-nav a{color:#fff;text-decoration:none;margin-right:26px}
.copyright{position:absolute;left:766px;top:20px}
.page-code{position:absolute;left:979px;top:18px;color:#c5d0e2}
</style>
</head>
<body>
<div class="page">
  <header class="site-header">
    <div class="brand"><span class="brand-square"></span>Torvel Capital</div>
    <div class="contact">Contact : Desmond Harlow &nbsp;- 555.014.2290<br>Mail : &nbsp;dharlow@torvelcapital.com</div>
  </header>

  <div class="hero" role="img" aria-label="Photograph of a city skyline with a tall skyscraper under a cloudy sky"></div>
  <nav class="main-nav">
    <a href="#">Home</a><a href="#">About</a><a href="#">Services</a><a href="#">Current Engagements</a><a href="#">Completed Transactions</a>
  </nav>
  <div class="hero-caption">Torvel Capital is an independent investment bank working for<br>buyers in a number of industries</div>
  <div class="hero-dots"><span></span><span class="off"></span><span></span></div>

  <div class="content"></div>

  <h2 style="left:97px;top:595px">Welcome To Our Website</h2>
  <p class="copy" style="left:103px;top:634px;width:478px">Torvel Capital is an independent investment bank working for buyers in a number of industries. We utilize exceptional technology in finding companies to meet our client's search criteria. We will not waste a buyer's time, a seller's time, or our own time.</p>
  <div class="world-map" role="img" aria-label="Dotted world map with location pins in North America, Asia and the Far East"></div>
  <a class="btn" href="#" style="left:111px;top:904px">Read more</a>

  <div class="divider"></div>

  <div class="service">
    <svg style="left:621px;top:602px" width="12" height="12" viewBox="0 0 12 12"><path d="M1 6h9M6 2l4 4-4 4" fill="none" stroke="#2d2d2d" stroke-width="1.4"/></svg>
    <h3 style="left:638px;top:594px">Strategic Advisory Services</h3>
    <p class="copy" style="left:640px;top:629px;width:300px">Lorem Ipsum, you need to be sure there isn't anything embarrassing hidden in the middle of text.</p>

    <svg style="left:621px;top:682px" width="12" height="12" viewBox="0 0 12 12"><path d="M1 6h9M6 2l4 4-4 4" fill="none" stroke="#2d2d2d" stroke-width="1.4"/></svg>
    <h3 style="left:638px;top:674px">Current Engagements</h3>
    <p class="copy" style="left:640px;top:709px;width:300px">Lorem Ipsum, you need to be sure there isn't anything embarrassing hidden in the middle of text.</p>

    <svg style="left:621px;top:761px" width="12" height="12" viewBox="0 0 12 12"><path d="M1 6h9M6 2l4 4-4 4" fill="none" stroke="#2d2d2d" stroke-width="1.4"/></svg>
    <h3 style="left:638px;top:753px">Completed Transactions</h3>
    <p class="copy" style="left:640px;top:788px;width:300px">Lorem Ipsum, you need to be sure there isn't anything embarrassing hidden in the middle of text.</p>

    <svg style="left:621px;top:841px" width="12" height="12" viewBox="0 0 12 12"><path d="M1 6h9M6 2l4 4-4 4" fill="none" stroke="#2d2d2d" stroke-width="1.4"/></svg>
    <h3 style="left:638px;top:833px">Regulatory Compliance</h3>
    <p class="copy" style="left:640px;top:868px;width:300px">Lorem Ipsum, you need to be sure there isn't anything embarrassing hidden in the middle of text.</p>
  </div>

  <h2 style="left:111px;top:963px">Our Process</h2>
  <p class="copy" style="left:111px;top:993px;width:378px">Lorem Ipsum, you need to be sure there isn't anything embarrassing hidden in the middle of text. All the Lorem Ipsum generators on the Internet tend to repeat predefined chunks as necessary</p>
  <a class="btn" href="#" style="left:111px;top:1052px">Read more</a>

  <h2 style="left:532px;top:963px">Our Team</h2>
  <p class="copy" style="left:534px;top:993px;width:378px">Lorem Ipsum, you need to be sure there isn't anything embarrassing hidden in the middle of text. All the Lorem Ipsum generators on the Internet tend to repeat predefined chunks as necessary</p>
  <a class="btn" href="#" style="left:534px;top:1052px">Read more</a>

  <section class="clients">
    <h2>Our Client</h2>
    <div class="client-list">
      <span>Varnholt</span><span>Kestrine</span><span>Ardomax</span><span><i></i>lumora</span><span>Quorra Labs</span><span>Belford</span><span>Tinwick Labs</span><span>Ostra</span>
    </div>
  </section>

  <footer class="site-footer">
    <nav class="footer-nav"><a href="#">Home</a><a href="#">About</a><a href="#">Services</a><a href="#">Current Engagements</a><a href="#">Completed Transactions</a><a href="#">Contact Us</a></nav>
    <div class="copyright">© 2014.www.torvelcapital.example</div>
    <div class="page-code">M1</div>
  </footer>
</div>
</body>
</html>
```